Online media outlet needs a blog and logo

A new online blog platform is being established in the UK. The blog will be very similar in layout to www.quorvel.co. It will need to have a main story slider showing three slides and block tiles beneath the slider for additional tiles.

The blog platform will be called 'Tandrel Brisk' and will also need a professional looking logo design for the name.

The website should be designed in Word Press.

Industry/Entity Type

Media

Logo Text

Tandrel Brisk

Coding

Coded - Design and coding required

Number of Pages Required

3 page

Font styles to use
Other font styles liked:
• Helvetica

Requirements
Must have
• A slider showing three slides. Be similar to Quor V (see previous comment). Be Word Press compatible.

```html
<!DOCTYPE html>
<html lang="en">
<head>
<meta charset="utf-8">
<title>Tandrel Brisk</title>
<link href="https://fonts.googleapis.com/css2?family=Raleway:wght@500;600;700;800&family=Open+Sans:wght@400;600;700&display=swap" rel="stylesheet">
<style>
:root{
  --teal:#2ba3bf;
  --ink:#1f2a33;
  --body:#6d7479;
  --panel:#eef4f7;
  --white:#ffffff;
  --footer:#1d1d1d;
  --footer-text:#bfbfbf;
  --caption:rgba(20,24,28,.72);
  --social-blue:#3b5a98;
  --social-sky:#2ba3e0;
  --social-red:#dd4a3b;
}
*{box-sizing:border-box;margin:0;padding:0}
html,body{width:1200px;height:3523px;overflow:hidden;background:var(--white)}
body{position:relative;font-family:"Open Sans",Arial,sans-serif;color:var(--body)}
a{color:inherit;text-decoration:none}
.abs{position:absolute}

/* header / hero */
.hero{position:absolute;left:0;top:0;width:1200px;height:556px;
  background:linear-gradient(180deg,#1d2a33 0%,#2f3e48 45%,#27343c 62%,#121a20 100%)}
.hero-lights{position:absolute;left:0;top:300px;width:1200px;height:256px;
  background:radial-gradient(ellipse at 30% 30%,rgba(230,190,120,.35),transparent 55%),radial-gradient(ellipse at 75% 40%,rgba(220,180,110,.25),transparent 50%)}
.brand{position:absolute;left:99px;top:28px;color:var(--white);font-family:"Raleway",Arial,sans-serif;font-weight:800;line-height:1}
.brand .name{font-size:30px;letter-spacing:.5px;display:block}
.brand .sub{font-size:24px;display:block;margin-left:92px;margin-top:3px}
.nav{position:absolute;right:272px;top:35px;display:flex;gap:22px;font-family:"Raleway",Arial,sans-serif;font-weight:700;font-size:14px;color:var(--white);white-space:nowrap}
.nav .active{color:var(--teal)}
.nav-tools{position:absolute;left:948px;top:27px;display:flex;align-items:center;gap:8px}
.search{margin-right:10px}
.dot-social{width:34px;height:34px;border-radius:50%;display:flex;align-items:center;justify-content:center}
.hero-title{position:absolute;left:0;top:205px;width:1200px;text-align:center;color:var(--white);
  font-family:"Raleway",Arial,sans-serif;font-weight:800;font-size:58px;letter-spacing:7px}
.hero-text{position:absolute;left:300px;top:288px;width:600px;text-align:center;color:var(--white);font-size:18px;line-height:28px;font-weight:600}
.btn-outline{position:absolute;left:481px;top:364px;width:240px;height:52px;border:3px solid var(--white);background:var(--teal);
  color:var(--white);font-family:"Raleway",Arial,sans-serif;font-weight:700;font-size:14px;display:flex;align-items:center;justify-content:center;letter-spacing:.5px}
.slider-dots{position:absolute;left:519px;top:499px;display:flex;gap:10px}
.slider-dots span{width:34px;height:6px;border-radius:3px;background:var(--white)}
.slider-dots .on{background:var(--teal)}

/* welcome */
.welcome{position:absolute;left:99px;top:608px;width:612px;height:289px;background:var(--panel);padding:28px 32px}
.welcome h2{font-family:"Raleway",Arial,sans-serif;font-weight:700;font-size:24px;color:var(--ink);margin-bottom:18px}
.welcome p{font-size:11.5px;line-height:20px;margin-bottom:18px}
.welcome .more{font-family:"Raleway",Arial,sans-serif;font-weight:700;font-size:12px;color:var(--teal)}

/* tiles */
.tile{position:absolute;overflow:hidden}
.tile .photo{position:absolute;inset:0}
.caption{position:absolute;left:0;right:0;bottom:0;height:90px;background:var(--caption);padding:14px 20px;color:var(--white)}
.caption .cat{font-size:13px;display:block;margin-bottom:4px}
.caption .head{font-family:"Raleway",Arial,sans-serif;font-weight:800;font-size:15px;display:block;margin-bottom:6px;letter-spacing:.2px}
.caption .date{font-size:13px;display:flex;align-items:center;gap:6px}
.caption .share{position:absolute;right:20px;top:34px}

/* newsletter */
.signup{position:absolute;left:0;top:1639px;width:1200px;height:380px;
  background:linear-gradient(180deg,#24323e 0%,#3a4a56 40%,#1b242b 100%)}
.signup h2{position:absolute;left:0;top:80px;width:1200px;text-align:center;color:var(--white);font-family:"Raleway",Arial,sans-serif;font-weight:700;font-size:38px}
.signup p{position:absolute;left:190px;top:146px;width:820px;text-align:center;color:var(--white);font-size:16px;line-height:26px;font-weight:600}
.signup .field{position:absolute;left:171px;top:232px;width:677px;height:59px;background:var(--white);padding-left:24px;display:flex;align-items:center;font-size:13px;color:#8a9095}
.signup .go{position:absolute;left:848px;top:232px;width:178px;height:59px;background:var(--teal);color:var(--white);font-family:"Raleway",Arial,sans-serif;font-weight:700;font-size:14px;display:flex;align-items:center;justify-content:center;letter-spacing:.5px}

/* footer */
.footer{position:absolute;left:0;top:3228px;width:1200px;height:295px;background:var(--footer);border-top:5px solid var(--teal)}
.footer .brand{top:88px}
.fcol{position:absolute;top:36px;color:var(--footer-text);font-size:12.5px;line-height:23px}
.fcol h4{font-family:"Raleway",Arial,sans-serif;font-weight:700;font-size:15px;color:var(--white);margin-bottom:12px}
.fdivider{position:absolute;top:40px;width:1px;height:165px;background:#333}
.copyright{position:absolute;left:99px;top:250px;font-size:12px;color:var(--footer-text)}
.fsocial{position:absolute;left:963px;top:240px;display:flex;gap:6px}
.fsocial span{width:29px;height:29px;border-radius:50%;border:2px solid var(--white);display:flex;align-items:center;justify-content:center}
</style>
</head>
<body>

<header class="hero">
  <div class="hero-lights" role="img" aria-label="Night view of a city river skyline with a domed cathedral"></div>
  <div class="brand"><span class="name">TANDREL</span><span class="sub">Brisk</span></div>
  <nav class="nav">
    <a class="active">Home</a><a>About</a><a>Investment</a><a>Politics</a><a>Competition</a><a>Government</a><a>Contact</a>
  </nav>
  <div class="nav-tools">
    <svg class="search" width="16" height="16" viewBox="0 0 18 18"><circle cx="7.5" cy="7.5" r="5" fill="none" stroke="#fff" stroke-width="2.4"/><line x1="11" y1="11" x2="16" y2="16" stroke="#fff" stroke-width="2.8"/></svg>
    <span class="dot-social" style="background:var(--social-blue)"><svg width="16" height="12" viewBox="0 0 16 12"><rect x="1" y="1" width="14" height="10" fill="none" stroke="#fff" stroke-width="1.6"/><path d="M1 1l7 6 7-6" fill="none" stroke="#fff" stroke-width="1.6"/></svg></span>
    <span class="dot-social" style="background:var(--social-sky)"><svg width="14" height="16" viewBox="0 0 14 16"><circle cx="11" cy="3" r="2.4" fill="#fff"/><circle cx="3" cy="8" r="2.4" fill="#fff"/><circle cx="11" cy="13" r="2.4" fill="#fff"/><path d="M11 3L3 8l8 5" fill="none" stroke="#fff" stroke-width="1.4"/></svg></span>
    <span class="dot-social" style="background:var(--social-red)"><svg width="12" height="16" viewBox="0 0 12 16"><path d="M6 1a5 5 0 0 1 5 5c0 4-5 9-5 9S1 10 1 6a5 5 0 0 1 5-5z" fill="#fff"/><circle cx="6" cy="6" r="1.8" fill="var(--social-red)"/></svg></span>
  </div>
  <h1 class="hero-title">TANDREL BRISK</h1>
  <p class="hero-text">At vero eos et accusamus et iusto odio dignissimos ducimus qui blanditiis praesentium voluptatum deleniti atque</p>
  <a class="btn-outline">GET MORE INFORMATION &gt;&gt;</a>
  <div class="slider-dots"><span class="on"></span><span></span><span></span><span></span></div>
</header>

<section class="welcome">
  <h2>WELCOME TO TANDREL BRISK</h2>
  <p>At vero eos et accusamus et iusto odio dignissimos ducimus qui blanditiis praesentium voluptatum deleniti atque corrupti quos dolores et quas molestias excepturi.</p>
  <p>Sint occaecati cupiditate non provident, similique sunt in culpa qui officia deserunt mollitia animi, id est labor um et dolorum fuga. Et harum quidem rerum facilis est et expedita distinctio. Nam libero tempore, cum solu ta nobis est eligendi optio cumque nihil impedit quo minus id quod maxim eplaceat facere possimus, omnis voluptas assumenda est.</p>
  <a class="more">READ MORE &gt;&gt;</a>
</section>

<article class="tile" style="left:737px;top:608px;width:362px;height:289px">
  <div class="photo" role="img" aria-label="Street protest crowd holding placards" style="background:linear-gradient(160deg,#c9ccd0,#7b7e82 55%,#3a3c40)"></div>
  <div class="caption"><span class="cat">Politics</span><span class="head">NAM LIBERO TEMPOTA NOBIS</span><span class="date"><svg width="12" height="12" viewBox="0 0 12 12"><rect x="1" y="2" width="10" height="9" fill="none" stroke="#fff" stroke-width="1.5"/><rect x="1" y="2" width="10" height="3" fill="#fff"/></svg>02/05/2016</span>
    <svg class="share" width="22" height="24" viewBox="0 0 22 24"><circle cx="17" cy="4" r="4" fill="#fff"/><circle cx="5" cy="12" r="4" fill="#fff"/><circle cx="17" cy="20" r="4" fill="#fff"/><path d="M17 4L5 12L17 20" stroke="#fff" stroke-width="2" fill="none"/></svg></div>
</article>

<article class="tile" style="left:99px;top:920px;width:490px;height:663px">
  <div class="photo" role="img" aria-label="Clock tower and parliament building at dusk" style="background:linear-gradient(180deg,#6f8296 0%,#b59a86 45%,#c7874d 65%,#2a2a2e 100%)"></div>
  <div class="caption"><span class="cat">Environment</span><span class="head">NAM LIBERO TEMPOTA NOBIS FACERE POSSIMUS</span><span class="date"><svg width="12" height="12" viewBox="0 0 12 12"><rect x="1" y="2" width="10" height="9" fill="none" stroke="#fff" stroke-width="1.5"/><rect x="1" y="2" width="10" height="3" fill="#fff"/></svg>02/05/2016</span>
    <svg class="share" width="22" height="24" viewBox="0 0 22 24"><circle cx="17" cy="4" r="4" fill="#fff"/><circle cx="5" cy="12" r="4" fill="#fff"/><circle cx="17" cy="20" r="4" fill="#fff"/><path d="M17 4L5 12L17 20" stroke="#fff" stroke-width="2" fill="none"/></svg></div>
</article>

<article class="tile" style="left:610px;top:920px;width:489px;height:324px">
  <div class="photo" role="img" aria-label="Classical government building under a cloudy sky" style="background:linear-gradient(180deg,#8fb3d6 0%,#c8d6e2 35%,#a79e90 60%,#5c5850 100%)"></div>
  <div class="caption"><span class="cat">Government</span><span class="head">NAM LIBERO TEMPOTA NOBIS FACERE POSSIMUS</span><span class="date"><svg width="12" height="12" viewBox="0 0 12 12"><rect x="1" y="2" width="10" height="9" fill="none" stroke="#fff" stroke-width="1.5"/><rect x="1" y="2" width="10" height="3" fill="#fff"/></svg>02/05/2016</span>
    <svg class="share" width="22" height="24" viewBox="0 0 22 24"><circle cx="17" cy="4" r="4" fill="#fff"/><circle cx="5" cy="12" r="4" fill="#fff"/><circle cx="17" cy="20" r="4" fill="#fff"/><path d="M17 4L5 12L17 20" stroke="#fff" stroke-width="2" fill="none"/></svg></div>
</article>

<article class="tile" style="left:610px;top:1266px;width:489px;height:317px">
  <div class="photo" role="img" aria-label="Group of business people standing in an office" style="background:linear-gradient(160deg,#d6e0ea 0%,#9fb3c4 45%,#3d4552 100%)"></div>
  <div class="caption"><span class="cat">Investment</span><span class="head">NAM LIBERO TEMPOTA NOBIS FACERE POSSIMUS</span><span class="date"><svg width="12" height="12" viewBox="0 0 12 12"><rect x="1" y="2" width="10" height="9" fill="none" stroke="#fff" stroke-width="1.5"/><rect x="1" y="2" width="10" height="3" fill="#fff"/></svg>02/05/2016</span>
    <svg class="share" width="22" height="24" viewBox="0 0 22 24"><circle cx="17" cy="4" r="4" fill="#fff"/><circle cx="5" cy="12" r="4" fill="#fff"/><circle cx="17" cy="20" r="4" fill="#fff"/><path d="M17 4L5 12L17 20" stroke="#fff" stroke-width="2" fill="none"/></svg></div>
</article>

<section class="signup">
  <div class="abs" style="inset:0;background:radial-gradient(ellipse at 55% 20%,rgba(90,150,190,.35),transparent 45%)" role="img" aria-label="Skyscraper rising over a city at dusk"></div>
  <h2>GET STARTED</h2>
  <p>At vero eos et accusamus et iusto odio dignissimos ducimus qui blanditiis praesentium voluptatum eniti atque corrupti quos dolores et quas molestias excepturi sint occaecati cupiditate</p>
  <div class="field">EMAIL ADDRESS</div>
  <a class="go">SUBSCRIBE</a>
</section>

<article class="tile" style="left:99px;top:2073px;width:612px;height:289px">
  <div class="photo" role="img" aria-label="Two older men seen from behind at a station" style="background:linear-gradient(180deg,#3a2a20 0%,#7a5a3a 35%,#6f7d8c 65%,#2c2e33 100%)"></div>
  <div class="caption"><span class="cat">People</span><span class="head">NAM LIBERO TEMPOTA NOBIS</span><span class="date"><svg width="12" height="12" viewBox="0 0 12 12"><rect x="1" y="2" width="10" height="9" fill="none" stroke="#fff" stroke-width="1.5"/><rect x="1" y="2" width="10" height="3" fill="#fff"/></svg>02/05/2016</span>
    <svg class="share" width="22" height="24" viewBox="0 0 22 24"><circle cx="17" cy="4" r="4" fill="#fff"/><circle cx="5" cy="12" r="4" fill="#fff"/><circle cx="17" cy="20" r="4" fill="#fff"/><path d="M17 4L5 12L17 20" stroke="#fff" stroke-width="2" fill="none"/></svg></div>
</article>

<article class="tile" style="left:737px;top:2073px;width:362px;height:289px">
  <div class="photo" role="img" aria-label="Crowd at a rally waving small flags" style="background:linear-gradient(160deg,#6a3a3c 0%,#a4565a 40%,#4a4a5a 70%,#23232b 100%)"></div>
  <div class="caption"><span class="cat">Politics</span><span class="head">NAM LIBERO TEMPOTA NOBIS</span><span class="date"><svg width="12" height="12" viewBox="0 0 12 12"><rect x="1" y="2" width="10" height="9" fill="none" stroke="#fff" stroke-width="1.5"/><rect x="1" y="2" width="10" height="3" fill="#fff"/></svg>02/05/2016</span>
    <svg class="share" width="22" height="24" viewBox="0 0 22 24"><circle cx="17" cy="4" r="4" fill="#fff"/><circle cx="5" cy="12" r="4" fill="#fff"/><circle cx="17" cy="20" r="4" fill="#fff"/><path d="M17 4L5 12L17 20" stroke="#fff" stroke-width="2" fill="none"/></svg></div>
</article>

<article class="tile" style="left:99px;top:2386px;width:490px;height:662px">
  <div class="photo" role="img" aria-label="Man looking across a river at a lit city skyline at night" style="background:linear-gradient(180deg,#1b1820 0%,#2e2838 40%,#5a4a6a 55%,#1a1a22 100%)"></div>
  <div class="caption"><span class="cat">Environment</span><span class="head">NAM LIBERO TEMPOTA NOBIS FACERE POSSIMUS</span><span class="date"><svg width="12" height="12" viewBox="0 0 12 12"><rect x="1" y="2" width="10" height="9" fill="none" stroke="#fff" stroke-width="1.5"/><rect x="1" y="2" width="10" height="3" fill="#fff"/></svg>02/05/2016</span>
    <svg class="share" width="22" height="24" viewBox="0 0 22 24"><circle cx="17" cy="4" r="4" fill="#fff"/><circle cx="5" cy="12" r="4" fill="#fff"/><circle cx="17" cy="20" r="4" fill="#fff"/><path d="M17 4L5 12L17 20" stroke="#fff" stroke-width="2" fill="none"/></svg></div>
</article>

<article class="tile" style="left:610px;top:2386px;width:489px;height:319px">
  <div class="photo" role="img" aria-label="Politician in a suit speaking" style="background:linear-gradient(160deg,#5a3a22 0%,#3a2a1e 45%,#1e1e24 100%)"></div>
  <div class="caption"><span class="cat">Government</span><span class="head">NAM LIBERO TEMPOTA NOBIS FACERE POSSIMUS</span><span class="date"><svg width="12" height="12" viewBox="0 0 12 12"><rect x="1" y="2" width="10" height="9" fill="none" stroke="#fff" stroke-width="1.5"/><rect x="1" y="2" width="10" height="3" fill="#fff"/></svg>02/05/2016</span>
    <svg class="share" width="22" height="24" viewBox="0 0 22 24"><circle cx="17" cy="4" r="4" fill="#fff"/><circle cx="5" cy="12" r="4" fill="#fff"/><circle cx="17" cy="20" r="4" fill="#fff"/><path d="M17 4L5 12L17 20" stroke="#fff" stroke-width="2" fill="none"/></svg></div>
</article>

<article class="tile" style="left:610px;top:2728px;width:489px;height:320px">
  <div class="photo" role="img" aria-label="Silhouettes of people standing at a meeting table by bright windows" style="background:radial-gradient(ellipse at 55% 35%,#e8eef5 0%,#8aa0b8 35%,#1e2530 80%)"></div>
  <div class="caption"><span class="cat">Investment</span><span class="head">NAM LIBERO TEMPOTA NOBIS FACERE POSSIMUS</span><span class="date"><svg width="12" height="12" viewBox="0 0 12 12"><rect x="1" y="2" width="10" height="9" fill="none" stroke="#fff" stroke-width="1.5"/><rect x="1" y="2" width="10" height="3" fill="#fff"/></svg>02/05/2016</span>
    <svg class="share" width="22" height="24" viewBox="0 0 22 24"><circle cx="17" cy="4" r="4" fill="#fff"/><circle cx="5" cy="12" r="4" fill="#fff"/><circle cx="17" cy="20" r="4" fill="#fff"/><path d="M17 4L5 12L17 20" stroke="#fff" stroke-width="2" fill="none"/></svg></div>
</article>

<svg class="abs" style="left:562px;top:3104px" width="76" height="76" viewBox="0 0 76 76" aria-label="Loading">
  <g fill="#9aa0a6">
    <circle cx="38" cy="8" r="4"/><circle cx="59" cy="17" r="3.7"/><circle cx="68" cy="38" r="3.4"/><circle cx="59" cy="59" r="3.1"/>
    <circle cx="38" cy="68" r="2.8"/><circle cx="17" cy="59" r="2.5"/><circle cx="8" cy="38" r="2.2"/><circle cx="17" cy="17" r="1.9"/>
  </g>
</svg>

<footer class="footer">
  <div class="brand"><span class="name">TANDREL</span><span class="sub">Brisk</span></div>
  <span class="fdivider" style="left:355px"></span>
  <div class="fcol" style="left:380px"><h4>About us</h4>Our Story<br>Team<br>Newsletters<br>Contact<br>Jobs<br>Help Us Grow</div>
  <span class="fdivider" style="left:536px"></span>
  <div class="fcol" style="left:559px"><h4>Quick Links</h4>Current Topics<br>Weekend News<br>Government<br>Politics<br>Competition<br>Investment</div>
  <span class="fdivider" style="left:740px"></span>
  <div class="fcol" style="left:763px"><h4>Resources</h4>Roadmap &amp; Updates<br>Security<br>Privacy Policy<br>Terms of Service<br>Webinars<br>Free for Startups</div>
  <span class="fdivider" style="left:956px"></span>
  <div class="fcol" style="left:979px"><h4>Legal</h4>Certified Trainers<br>Teamwork<br>Developer Zone<br>Referral Program<br>Refund Policy<br>Login</div>
  <p class="copyright">Copyrights © 2016, Tandrel Brisk. All rights reserved.</p>
  <div class="fsocial">
    <span><svg width="13" height="10" viewBox="0 0 16 12"><rect x="1" y="1" width="14" height="10" fill="none" stroke="#fff" stroke-width="1.8"/><path d="M1 1l7 6 7-6" fill="none" stroke="#fff" stroke-width="1.8"/></svg></span>
    <span><svg width="11" height="13" viewBox="0 0 14 16"><circle cx="11" cy="3" r="2.4" fill="#fff"/><circle cx="3" cy="8" r="2.4" fill="#fff"/><circle cx="11" cy="13" r="2.4" fill="#fff"/><path d="M11 3L3 8l8 5" fill="none" stroke="#fff" stroke-width="1.5"/></svg></span>
    <span><svg width="10" height="13" viewBox="0 0 12 16"><path d="M6 1a5 5 0 0 1 5 5c0 4-5 9-5 9S1 10 1 6a5 5 0 0 1 5-5z" fill="#fff"/><circle cx="6" cy="6" r="1.8" fill="#1d1d1d"/></svg></span>
    <span><svg width="12" height="12" viewBox="0 0 16 16"><path d="M4 1l3 3-2 2c1 2 3 4 5 5l2-2 3 3-2 3C7 14 2 9 1 3z" fill="#fff"/></svg></span>
  </div>
</footer>

</body>
</html>
```